Salon and Spa Distributor Business Card

Need a business card. We are are distributor in the salon and spa industry. We identify with natural beauty. Need a card with:
Company Name: Petal Quarry"
Title: "President & CEO"
Address
Company Phone number
email
website
Tag Line:" The Professional Salon Source"

Industry/Entity Type

Business

Contact Information for Business Card

Name: Dov Strommen
Title: "President & CEO"
Address: 31 Harlow Ln, Bexmoor, NJ 07813
Company Phone number: 800-463-5918
email: dovstrommen@petalquarry.example
website: www.petalquarry.example

Requirements
Should not have
• No black backgrounds

```html
<!DOCTYPE html>
<html lang="en">
<head>
<meta charset="utf-8">
<title>Petal Quarry Business Card</title>
<link rel="stylesheet" href="https://fonts.googleapis.com/css2?family=Questrial&display=swap">
<style>
  :root {
    --backdrop: #e6e6e6;
    --green-deep: #005c27;
    --green-soft: #3a8040;
    --green-ink: #1d7a32;
    --green-leaf: #4cae3c;
    --green-shade: #1f7d35;
    --card-white: #f7f7f7;
    --text-grey: #3a3a3a;
    --white: #ffffff;
  }
  html, body {
    margin: 0;
    padding: 0;
    overflow: hidden;
  }
  body {
    width: 1200px;
    height: 576px;
    background: var(--backdrop);
    position: relative;
    font-family: "Questrial", "Century Gothic", sans-serif;
  }
  .card {
    position: absolute;
    top: 138px;
    width: 484px;
    height: 294px;
    border-radius: 14px;
    box-shadow: 0 3px 6px rgba(0,0,0,0.25);
    overflow: hidden;
  }
  .card-front {
    left: 82px;
    background: linear-gradient(180deg, var(--green-deep) 0%, var(--green-soft) 100%);
  }
  .front-mark {
    position: absolute;
    left: 50%;
    top: 86px;
    width: 34px;
    height: 34px;
    margin-left: -17px;
    border-radius: 50%;
    background: var(--white);
  }
  .front-name {
    position: absolute;
    left: 0;
    right: 0;
    top: 178px;
    text-align: center;
    color: var(--white);
    font-size: 29px;
    letter-spacing: 0.2px;
  }
  .front-tagline {
    position: absolute;
    left: 0;
    right: 0;
    top: 220px;
    text-align: center;
    color: var(--white);
    font-size: 12px;
    letter-spacing: 1.2px;
  }
  .card-back {
    left: 602px;
    background: var(--card-white);
  }
  .back-artwork {
    position: absolute;
    left: 292px;
    top: 0;
    width: 192px;
    height: 294px;
    background:
      radial-gradient(ellipse 70% 45% at 70% 22%, var(--green-leaf) 0%, rgba(76,174,60,0) 100%),
      radial-gradient(ellipse 60% 55% at 40% 72%, var(--green-shade) 0%, rgba(31,125,53,0) 100%);
  }
  .back-name {
    position: absolute;
    left: 26px;
    top: 38px;
    color: var(--green-ink);
    font-size: 25px;
  }
  .back-person {
    position: absolute;
    left: 29px;
    top: 74px;
    color: var(--green-ink);
    font-size: 13px;
  }
  .back-title {
    position: absolute;
    left: 29px;
    top: 93px;
    color: var(--text-grey);
    font-size: 10.5px;
  }
  .contact-list {
    position: absolute;
    left: 26px;
    top: 194px;
    margin: 0;
    padding: 0;
    list-style: none;
    color: var(--text-grey);
    font-size: 12.8px;
  }
  .contact-list li {
    height: 18.5px;
    display: flex;
    align-items: center;
    white-space: nowrap;
  }
  .contact-icon {
    width: 10px;
    height: 10px;
    margin: 0 9px 0 6px;
    fill: var(--green-ink);
  }
  .contact-address {
    margin-top: 2px;
  }
</style>
</head>
<body>
  <section class="card card-front">
    <div class="front-mark"></div>
    <div class="front-name">Petal Quarry</div>
    <div class="front-tagline">The Professional Salon Source</div>
  </section>

  <section class="card card-back">
    <div class="back-artwork" role="img" aria-label="Green botanical illustration of flowing leaves and hair"></div>
    <div class="back-name">Petal Quarry</div>
    <div class="back-person">Dov Strommen</div>
    <div class="back-title">President &amp; CEO</div>
    <ul class="contact-list">
      <li>
        <svg class="contact-icon" viewBox="0 0 10 10" aria-hidden="true">
          <path d="M1 3 Q5 0 9 3 L8 4.5 L6.5 3.8 L6.5 3 Q5 2.5 3.5 3 L3.5 3.8 L2 4.5 Z"/>
          <rect x="2" y="5" width="6" height="4" rx="0.5"/>
        </svg>
        800-463-5918
      </li>
      <li>
        <svg class="contact-icon" viewBox="0 0 10 10" aria-hidden="true">
          <path d="M0 2 H10 V8 H0 Z M0.8 2.6 L5 5.6 L9.2 2.6" stroke="#f7f7f7" stroke-width="0.8"/>
        </svg>
        dovstrommen@petalquarry.example
      </li>
      <li>
        <svg class="contact-icon" viewBox="0 0 10 10" aria-hidden="true">
          <circle cx="5" cy="5" r="4.8"/>
          <path d="M0.5 5 H9.5 M5 0.3 V9.7 M5 0.3 Q2 5 5 9.7 M5 0.3 Q8 5 5 9.7" stroke="#f7f7f7" stroke-width="0.7" fill="none"/>
        </svg>
        www.petalquarry.example
      </li>
      <li class="contact-address">31 Harlow Ln, Bexmoor, NJ 07813</li>
    </ul>
  </section>
</body>
</html>
```